Business Card for Professional Photographer

I'm looking for an eye catching modern clean design that compliments my logo/ website fonts & colours.
I specialise in architecture, corporate & commercial photography so I'm marketing to professional clients rather than portrait / wedding clients.

I would prefer to not have a solid black design.

My logo brand guide is as follows :

Main front font. : Reislust
Main font colour : #fff
Slogan front font : Ubuntu Bold
Monogram front font : Venti Medium
Container colour : #fff

I need print ready files in pdf .png & .eps formats.

Included in the files below are some screen grabs as reference to font & colours etc.

```html
<!DOCTYPE html>
<html lang="en">
<head>
<meta charset="utf-8">
<title>Clearline Studio – Business Card</title>
<link rel="stylesheet" href="https://fonts.googleapis.com/css2?family=Ubuntu:wght@400;500;700&family=Roboto:wght@400&display=swap">
<style>
  :root {
    --backdrop: #3b3b3c;
    --card: #1c1c1d;
    --card-edge: #262627;
    --gold: #d4a94a;
    --gold-light: #f1d27e;
    --gold-deep: #a97d2a;
    --white: #ffffff;
    --ink: #1a1a1a;
  }
  * { box-sizing: border-box; margin: 0; padding: 0; }
  html, body {
    width: 799px; height: 1200px; overflow: hidden;
    background: var(--backdrop);
  }
  .canvas {
    position: relative; width: 799px; height: 1200px;
    display: flex; flex-direction: column; align-items: center;
    justify-content: space-around; padding: 70px 0;
  }
  .card {
    position: relative; width: 640px; height: 366px;
    background: var(--card);
    border: 1px solid var(--card-edge);
    overflow: hidden;
    font-family: "Roboto", sans-serif;
  }

  /* Front */
  .card-front .brand {
    position: absolute; left: 0; right: 0; top: 128px;
    display: flex; align-items: center; justify-content: center; gap: 16px;
  }
  .brand-dot {
    width: 26px; height: 26px; border-radius: 50%;
    border: 3px solid var(--gold);
  }
  .brand-name {
    font-family: "Ubuntu", sans-serif; font-weight: 500;
    font-size: 34px; letter-spacing: 4px; color: var(--gold);
  }
  .card-front .website {
    position: absolute; left: 0; right: 0; top: 246px; text-align: center;
    font-family: "Ubuntu", sans-serif; font-size: 16px; letter-spacing: 3px;
    color: var(--gold);
  }

  /* Back */
  .holder { position: absolute; left: 44px; top: 50px; }
  .holder-name {
    font-family: "Ubuntu", sans-serif; font-weight: 700;
    font-size: 22px; color: var(--gold);
  }
  .holder-role { font-size: 14px; color: var(--white); margin-top: 2px; }

  .contacts {
    position: absolute; left: 44px; top: 196px; list-style: none;
  }
  .contacts li {
    display: flex; align-items: center; gap: 12px;
    font-size: 15px; color: var(--white); line-height: 22px;
  }
  .contacts svg { width: 13px; height: 13px; fill: var(--gold); flex: none; }

  .back-brand {
    position: absolute; left: 330px; width: 280px; top: 140px; text-align: center;
  }
  .back-brand .brand-name { font-size: 24px; letter-spacing: 3px; }
  .slogan {
    font-family: "Ubuntu", sans-serif; font-weight: 700;
    font-size: 10px; letter-spacing: 1.6px; color: var(--gold-deep);
    margin-top: 6px;
  }

  .gold-band { position: absolute; left: 0; bottom: 0; width: 640px; height: 80px; }
  .address {
    position: absolute; left: 340px; right: 20px; bottom: 16px;
    font-size: 17px; color: var(--ink); text-align: center;
  }
</style>
</head>
<body>
<main class="canvas">

  <section class="card card-front" aria-label="Card front">
    <div class="brand">
      <span class="brand-dot"></span>
      <span class="brand-name">CLEARLINE STUDIO</span>
    </div>
    <p class="website">www.clearlinestudio.com.au</p>
  </section>

  <section class="card card-back" aria-label="Card back">
    <div class="holder">
      <p class="holder-name">Mara Ellison</p>
      <p class="holder-role">Photographer</p>
    </div>

    <ul class="contacts">
      <li>
        <svg viewBox="0 0 16 16" aria-hidden="true"><path d="M3 1h3l1.5 4-2 1.3a9 9 0 0 0 4.2 4.2L11 8.5l4 1.5v3a2 2 0 0 1-2 2A12 12 0 0 1 1 3a2 2 0 0 1 2-2z"/></svg>
        0400123456
      </li>
      <li>
        <svg viewBox="0 0 16 16" aria-hidden="true"><path d="M1 3h14v10H1z M2 4.2V12h12V4.2L8 8.6z" fill-rule="evenodd"/></svg>
        info@clearlinestudio.com.au
      </li>
      <li>
        <svg viewBox="0 0 16 16" aria-hidden="true"><path d="M8 1a7 7 0 1 0 0 14A7 7 0 0 0 8 1zm0 1.4c.9 0 1.9 1.7 2.2 4.6H5.8C6.1 4.1 7.1 2.4 8 2.4zM2.5 7h2.2c.1-1.6.4-3 .9-3.9A5.6 5.6 0 0 0 2.5 7zm0 2a5.6 5.6 0 0 0 3.1 3.9c-.5-.9-.8-2.3-.9-3.9zm3.3 0h4.4c-.3 2.9-1.3 4.6-2.2 4.6S6.1 11.9 5.8 9zm5.5 0c-.1 1.6-.4 3-.9 3.9A5.6 5.6 0 0 0 13.5 9zm2.2-2a5.6 5.6 0 0 0-3.1-3.9c.5.9.8 2.3.9 3.9z"/></svg>
        www.clearlinestudio.com.au
      </li>
    </ul>

    <div class="back-brand">
      <p class="brand-name">CLEARLINE STUDIO</p>
      <p class="slogan">Architecture Corporate Commercial</p>
    </div>

    <svg class="gold-band" viewBox="0 0 640 80" aria-hidden="true">
      <defs>
        <linearGradient id="goldFoil" x1="0" y1="0" x2="1" y2="0.3">
          <stop offset="0" stop-color="#a97d2a"/>
          <stop offset="0.35" stop-color="#f1d27e"/>
          <stop offset="0.6" stop-color="#c99a3c"/>
          <stop offset="1" stop-color="#f3dc97"/>
        </linearGradient>
      </defs>
      <path d="M0 58 H300 Q310 14 346 14 H640 V80 H0 Z" fill="url(#goldFoil)"/>
    </svg>
    <p class="address">8 Harbour Lane Portside Vic 3999</p>
  </section>

</main>
</body>
</html>
```